New career and executive coaching business needs a business card design including logo

Company name: 'Bramblefield Growth Partners.' The aim of my coaching engagements is to help people improve their communication in the workplace and achieve their career goals. The process involves working with individuals to help them uncover their strengths and talents, then leverage those to improve their working lives. The Tarwick Inventory is the starting point to the process. I am after an exciting and interesting business card design (including logo)which is professional yet will still get people's attention.

Industry/Entity Type

Business

Contact Information for Business Card

Name: Malcolm Dervaney
Position: Owner
Address: 58 Quorrin Ct, Elmbridge Vic 3190
Phone: 0418923047
Website: bramblefieldgrowth.com.au
Email: malcolm@bgp.com.au

Colors
33a6d7
00a990
0355a3
3176b5

Requirements
Must have
• logo

```html
<!DOCTYPE html>
<html lang="en">
<head>
<meta charset="utf-8">
<title>Bramblefield Growth Partners – Business Card</title>
<link rel="stylesheet" href="https://fonts.googleapis.com/css2?family=Open+Sans:wght@400;600;700&display=swap">
<style>
  :root {
    --backdrop: #2b2c30;
    --card-white: #ffffff;
    --ink-dark: #1a1a1a;
    --sky-blue: #33a6d7;
    --mid-blue: #3176b5;
    --deep-blue: #0355a3;
    --text-light: #ffffff;
  }
  * { margin: 0; padding: 0; box-sizing: border-box; }
  html, body {
    width: 1200px;
    height: 864px;
    overflow: hidden;
    background: var(--backdrop);
    font-family: "Open Sans", Arial, sans-serif;
  }
  .canvas { position: relative; width: 1200px; height: 864px; }
  .card {
    position: absolute;
    width: 600px;
    height: 330px;
    border-radius: 4px;
    box-shadow: 0 12px 26px rgba(0,0,0,0.5);
    overflow: hidden;
  }

  /* Front */
  .card-front {
    left: 300px;
    top: 70px;
    background: var(--card-white);
  }
  .front-brand {
    position: absolute;
    left: 0;
    right: 0;
    top: 78px;
    display: flex;
    flex-direction: column;
    align-items: center;
    gap: 22px;
  }
  .brand-square {
    width: 78px;
    height: 78px;
    background: var(--deep-blue);
    transform: rotate(45deg);
  }
  .front-brand-name {
    font-weight: 600;
    font-size: 30px;
    color: var(--ink-dark);
    margin-top: 14px;
  }

  /* Back */
  .card-back {
    left: 190px;
    top: 440px;
    background: linear-gradient(175deg, var(--sky-blue) 0%, var(--mid-blue) 50%, var(--deep-blue) 100%);
    color: var(--text-light);
  }
  .back-graphic {
    position: absolute;
    right: 0;
    top: 0;
    width: 270px;
    height: 100%;
    border-top-left-radius: 140px 165px;
    border-bottom-left-radius: 140px 165px;
    background: linear-gradient(160deg, rgba(49,118,181,0.55) 0%, rgba(3,85,163,0.9) 100%);
  }
  .back-content {
    position: relative;
    padding: 28px 36px;
  }
  .back-brand-name {
    font-weight: 600;
    font-size: 25px;
    line-height: 1.1;
  }
  .holder-name {
    margin-top: 22px;
    font-weight: 700;
    font-size: 17px;
  }
  .holder-role { font-size: 13px; margin-top: 1px; }
  .address {
    margin-top: 18px;
    font-size: 13px;
    line-height: 1.65;
    font-style: normal;
  }
  .contact-list {
    list-style: none;
    margin-top: 16px;
    font-size: 14px;
    line-height: 1.6;
  }
  .contact-list li { display: flex; align-items: center; gap: 8px; }
  .contact-icon { width: 12px; height: 12px; fill: var(--text-light); flex: none; }
</style>
</head>
<body>
<main class="canvas">
  <section class="card card-front" aria-label="Business card front">
    <div class="front-brand">
      <span class="brand-square"></span>
      <span class="front-brand-name">Bramblefield Growth Partners</span>
    </div>
  </section>

  <section class="card card-back" aria-label="Business card back">
    <div class="back-graphic" role="img" aria-label="Large decorative brand graphic in deep blue tones"></div>
    <div class="back-content">
      <div class="back-brand-name">Bramblefield Growth Partners</div>
      <div class="holder-name">Malcolm Dervaney</div>
      <div class="holder-role">Owner</div>
      <address class="address">58 Quorrin Ct,<br>Elmbridge Vic 3190</address>
      <ul class="contact-list">
        <li>
          <svg class="contact-icon" viewBox="0 0 24 24" aria-hidden="true"><path d="M6.6 10.8a15.1 15.1 0 0 0 6.6 6.6l2.2-2.2a1 1 0 0 1 1-.25 11.4 11.4 0 0 0 3.6.57 1 1 0 0 1 1 1V20a1 1 0 0 1-1 1A17 17 0 0 1 3 4a1 1 0 0 1 1-1h3.5a1 1 0 0 1 1 1c0 1.25.2 2.45.57 3.57a1 1 0 0 1-.25 1z"/></svg>
          <span>0418923047</span>
        </li>
        <li>
          <svg class="contact-icon" viewBox="0 0 24 24" aria-hidden="true"><path d="M2 5h20v14H2z M2 5l10 8 10-8" fill="none" stroke="#fff" stroke-width="2"/><path d="M3 6h18l-9 7z"/></svg>
          <span>malcolm@bgp.com.au</span>
        </li>
        <li>
          <svg class="contact-icon" viewBox="0 0 24 24" aria-hidden="true"><circle cx="12" cy="12" r="10" fill="none" stroke="#fff" stroke-width="2"/><path d="M2 12h20M12 2c3 3 3 17 0 20M12 2c-3 3-3 17 0 20" fill="none" stroke="#fff" stroke-width="1.6"/></svg>
          <span>bramblefieldgrowth.com.au</span>
        </li>
      </ul>
    </div>
  </section>
</main>
</body>
</html>
```